Exclusive beauty salon needs a price list or services booklet

I need a new very attractive flyer for my beauty salon, containing information on the different services and their prices.
In attachment you can find a pdf of the "old" one, but I'd love to have a beautifully designed new one!
I'd love to have a booklet in format 148 x 148 mm, or in US format, containing 12 or 16 pages, but if you can offer other nice looking designs they are welcome!
The services that need to come in the booklet with their prices can all be found on my website: www.atelierverano.be, starting with
Gelaatsverzorging
Wimperverlenging
Suikerontharing
Wimperlifting
Permanente Make Up
Airbrush Tanning

Target Market(s)

woman from 20 to 89 years old

Industry/Entity Type

Beauty Salon

Font styles to use
Sans Serif

Colors

Designer to choose colors to be used in the design.

Requirements
Must have
• a classy nice look, it must contain details about the services from my beauty salon and their prices, and nice pictures.
• The Names, prices and explanations of the services can easily be found on my website: www.atelierverano.be
Nice to have
• In attachment you can find the "old" price list in pdf, what I need now is a "new booklet" with the new logo and updated services price list.
• I need a very nice and attractive looking booklet, classy chique, Paris chique, looking very expensive.
Should not have
• Not too much colors, not too curly, but still feminine

```html
<!DOCTYPE html>
<html lang="nl">
<head>
<meta charset="utf-8">
<title>Atelier Verano – Prijslijst</title>
<link href="https://fonts.googleapis.com/css2?family=Open+Sans:wght@300;400;600&display=swap" rel="stylesheet">
<style>
:root{
  --bg:#e6e6e7;
  --paper:#ffffff;
  --rose:#e2a6ad;
  --rose-soft:#f3d9dc;
  --mint:#a9d9d3;
  --mint-soft:#e3f3f1;
  --ink:#6d6d6d;
  --ink-light:#9a9a9a;
  --photo-skin:#e9d3c6;
  --photo-warm:#d8b9a6;
}
*{margin:0;padding:0;box-sizing:border-box}
html,body{width:1200px;height:4337px;overflow:hidden;background:var(--bg)}
body{position:relative;font-family:"Open Sans",Arial,sans-serif;color:var(--ink);font-weight:300}
.spread{position:absolute;left:110px;width:980px;height:450px;display:flex;box-shadow:0 3px 10px rgba(0,0,0,.12)}
.spread.single-right{left:600px;width:490px}
.spread.single-left{width:490px}
.page{position:relative;width:490px;height:450px;background:var(--paper);overflow:hidden}
.page + .page{border-left:1px solid #eee}
.photo{position:absolute;background:linear-gradient(135deg,var(--photo-skin),var(--photo-warm))}
.photo.cool{background:linear-gradient(135deg,#f1ece9,#d9cfc9)}
.photo.mint{background:linear-gradient(135deg,#f4efe9,#cfe6e1)}
.photo.round{border-radius:50%}
.title{position:absolute;font-size:13px;letter-spacing:1.5px;text-transform:uppercase;font-weight:400}
.title.rose{color:var(--rose)}
.title.mint{color:var(--mint)}
.bar{position:absolute;height:16px;display:flex;justify-content:space-between;align-items:center;padding:0 8px;font-size:7.5px;letter-spacing:.8px;text-transform:uppercase;color:#fff;font-weight:600}
.bar.rose{background:var(--rose)}
.bar.mint{background:var(--mint)}
.bar.soft-mint{background:var(--mint-soft);color:var(--ink)}
.bar.soft-mint .price{color:var(--ink-light)}
.text{position:absolute;font-size:7px;line-height:1.65;color:var(--ink)}
.text p + p{margin-top:5px}
.text ul{list-style:none}
.text li::before{content:"– ";color:var(--rose)}
.brand-mark{position:absolute;right:22px;bottom:16px;display:flex;align-items:center;gap:4px;font-size:6px;letter-spacing:1.2px;color:var(--ink-light);font-weight:400}
.brand-mark i{width:7px;height:7px;border-radius:50%;background:var(--rose);display:block}
.quote-box{position:absolute;border-left:2px solid var(--rose-soft);padding-left:10px}
.panel{position:absolute;background:var(--mint-soft);padding:14px}
.caption{position:absolute;font-size:7.5px;color:var(--rose)}
.logo-text{position:absolute;font-size:18px;letter-spacing:3px;color:var(--ink);font-weight:400}
.testimonial{text-align:center;font-size:7.5px;line-height:1.7}
.testimonial .who{color:var(--rose);font-size:6.5px;letter-spacing:1px;margin-top:4px}
</style>
</head>
<body>

<!-- Spread 1 : welcome -->
<section class="spread single-right" style="top:10px">
  <div class="page">
    <div class="photo cool" style="left:40px;top:40px;width:100px;height:100px" role="img" aria-label="Portretfoto van de schoonheidsspecialiste"></div>
    <div class="bar mint" style="left:0;top:115px;width:490px;height:22px;padding-left:160px;font-size:10px;text-transform:none;letter-spacing:.5px">Hoe kan ik u helpen?</div>
    <div class="text" style="left:160px;top:155px;width:300px">
      <p>Al meer dan tien jaar help ik vrouwen zich mooi en zelfzeker te voelen. In mijn salon neem ik alle tijd om samen met u naar uw wensen te luisteren en een behandeling op maat te kiezen. Mijn specialiteiten zijn gelaatsverzorging met exclusieve producten, wimperverlenging, suikerontharing, airbrush tanning en permanente make up.</p>
    </div>
  </div>
</section>

<!-- Spread 2 : permanente make up -->
<section class="spread" style="top:490px">
  <div class="page">
    <div class="title rose" style="right:30px;top:28px">Permanente make up</div>
    <div class="photo" style="left:0;top:55px;width:290px;height:185px" role="img" aria-label="Close-up van een gesloten oog met wimperpad"></div>
    <div class="quote-box" style="left:150px;top:265px;width:300px">
      <div class="text" style="position:static;font-size:6.5px;color:var(--ink-light);letter-spacing:1px;text-transform:uppercase">Gratis adviesgesprek</div>
      <div class="text" style="position:static;margin-top:4px">Het is mogelijk om eerst een vrijblijvend gesprek te voeren om uw wensen te bespreken. We kiezen samen de kleur en de vorm die het best bij uw gezicht passen, zodat het resultaat natuurlijk en stralend blijft. Zo weet u vooraf precies wat u mag verwachten.</div>
    </div>
  </div>
  <div class="page">
    <div class="bar rose" style="left:30px;top:26px;width:430px"><span>Full lips</span><span class="price">€ 350</span></div>
    <div class="text" style="left:30px;top:48px;width:300px">
      <p>Een natuurlijke lipcontour met een zachte kleur die de lippen voller doet lijken.</p>
      <p>Het resultaat blijft twee tot drie jaar mooi. Een nazorgbehandeling na zes weken is inbegrepen in de prijs.</p>
    </div>
    <div class="photo" style="left:360px;top:46px;width:90px;height:56px" role="img" aria-label="Foto van lippen met permanente make up"></div>
    <div class="bar mint" style="left:30px;top:125px;width:430px"><span>Permanente make up volledige oogcontour</span><span class="price">€ 300</span></div>
    <div class="text" style="left:30px;top:147px;width:300px">
      <p>Een fijne lijn boven en onder de wimpers die de ogen meer diepte en uitstraling geeft.</p>
      <p>Ideaal voor wie elke ochtend tijd wil winnen of gevoelige ogen heeft.</p>
    </div>
    <div class="photo" style="left:360px;top:145px;width:90px;height:56px" role="img" aria-label="Foto van een oog met eyeliner"></div>
    <div class="bar rose" style="left:30px;top:225px;width:430px"><span>Wenkbrauw met poeder</span><span class="price">€ 320</span></div>
    <div class="text" style="left:30px;top:247px;width:300px">
      <p>Een zachte poedertechniek die de wenkbrauwen een gevuld en verzorgd uiterlijk geeft.</p>
      <p>Na de behandeling ontvangt u een nazorgset en duidelijke instructies voor thuis.</p>
    </div>
    <div class="brand-mark"><i></i>ATELIER VERANO</div>
  </div>
</section>

<!-- Spread 3 : wenkbrauwen -->
<section class="spread" style="top:970px">
  <div class="page">
    <div class="bar rose" style="left:30px;top:26px;width:430px"><span>Pure eyeliner boven met oog</span><span class="price">€ 180</span></div>
    <div class="text" style="left:30px;top:48px;width:300px">
      <p>Een subtiele lijn tussen de wimpers voor een open en frisse blik.</p>
      <ul><li>geschikt voor lenzendragers</li><li>snelle genezing</li><li>natuurlijk resultaat</li></ul>
    </div>
    <div class="photo" style="left:360px;top:46px;width:90px;height:56px" role="img" aria-label="Foto van een oog met fijne eyeliner"></div>
    <div class="bar mint" style="left:30px;top:130px;width:430px"><span>Wenkbrauwen haartjes techniek</span><span class="price">€ 280</span></div>
    <div class="text" style="left:30px;top:152px;width:300px">
      <ul><li>elk haartje wordt apart getekend</li><li>ideaal bij dunne of lege plekken</li><li>zeer natuurlijk effect</li><li>duurt twee tot drie jaar</li></ul>
    </div>
    <div class="photo" style="left:360px;top:150px;width:90px;height:56px" role="img" aria-label="Foto van wenkbrauw met haartjestechniek"></div>
    <div class="bar rose" style="left:30px;top:235px;width:430px"><span>Wenkbrauwen shading brow of poederwenkbrauw</span><span class="price">€ 290</span></div>
    <div class="text" style="left:30px;top:257px;width:300px">
      <ul><li>zachte schaduw zonder harde lijnen</li><li>geschikt voor elk huidtype</li><li>lijkt op licht opgebrachte poeder</li><li>kleur op maat gemengd</li></ul>
    </div>
    <div class="photo" style="left:360px;top:255px;width:90px;height:56px" role="img" aria-label="Foto van wenkbrauw met poedertechniek"></div>
  </div>
  <div class="page">
    <div class="bar mint" style="left:30px;top:26px;width:430px"><span>Wenkbrauw power brow</span><span class="price">€ 320</span></div>
    <div class="text" style="left:30px;top:48px;width:300px">
      <ul><li>combinatie van haartjes en schaduw</li><li>vol en gedefinieerd resultaat</li><li>perfect voor een sprekende look</li><li>inclusief nazorgbehandeling</li></ul>
    </div>
    <div class="panel" style="left:30px;top:150px;width:430px;height:160px">
      <div class="text" style="position:static">
        <p>Voor een mooi en duurzaam resultaat is een goede voorbereiding belangrijk. Lees onderstaande tips aandachtig voor u een afspraak maakt.</p>
        <ul style="margin-top:6px"><li>geen alcohol of koffie op de dag van de behandeling</li><li>geen bloedverdunners enkele dagen vooraf</li><li>twee weken geen zonnebank of zwembad</li><li>geen peeling of botox in de maand voordien</li><li>volg de nazorg zorgvuldig op</li></ul>
      </div>
    </div>
    <div class="brand-mark"><i></i>ATELIER VERANO</div>
  </div>
</section>

<!-- Spread 4 : gelaatsverzorging -->
<section class="spread" style="top:1450px">
  <div class="page">
    <div class="title mint" style="right:30px;top:28px">Gelaatsverzorging</div>
    <div class="bar soft-mint" style="left:30px;top:75px;width:270px"><span>Cosmetische verzorging</span><span class="price">€ 55</span></div>
    <div class="bar mint" style="left:30px;top:110px;width:270px"><span>Reinigende gezichtsverzorging</span><span class="price">€ 65</span></div>
    <div class="bar soft-mint" style="left:30px;top:145px;width:270px"><span>Vitaal nettoyage</span><span class="price">€ 70 – € 80</span></div>
    <div class="bar mint" style="left:30px;top:180px;width:270px"><span>Hydratation essentielle</span><span class="price">€ 75 – € 85</span></div>
    <div class="bar soft-mint" style="left:30px;top:215px;width:270px"><span>Pureté essentielle</span><span class="price">€ 75 – € 85</span></div>
    <div class="bar mint" style="left:30px;top:250px;width:270px"><span>Luxe verzorging supreme experience</span><span class="price">€ 95 – € 110</span></div>
  </div>
  <div class="page">
    <div class="logo-text" style="left:230px;top:30px">MAISON ALBA</div>
    <div class="photo mint" style="left:0;top:70px;width:490px;height:210px" role="img" aria-label="Vrouw met stralende huid naast flesjes verzorgingsproducten"></div>
    <div class="caption" style="left:30px;top:295px">Gelaatsverzorging met de exclusieve producten van Maison Alba</div>
    <div class="text" style="left:30px;top:310px;width:300px;color:var(--ink-light)">Elke behandeling begint met een huidanalyse.</div>
    <div class="brand-mark"><i></i>ATELIER VERANO</div>
  </div>
</section>

<!-- Spread 5 : wimperverlenging -->
<section class="spread" style="top:1930px">
  <div class="page">
    <div class="title rose" style="left:30px;top:24px;font-size:11px">Individuele wimperverlenging lash creations</div>
    <div class="text" style="left:30px;top:44px;width:420px;color:var(--ink-light)">Langere, vollere wimpers zonder mascara, elke dag opnieuw.</div>
    <div class="text" style="left:30px;top:64px;width:300px">
      <p>Bij een wimperverlenging wordt op elke natuurlijke wimper een losse kunstwimper geplaatst. Zo ontstaat een natuurlijk en verzorgd resultaat dat enkele weken blijft.</p>
      <p>De lengte, dikte en krul worden afgestemd op uw ogen en uw persoonlijke stijl.</p>
      <p>Voor een blijvend mooi effect raden we een opvulbeurt aan om de twee tot drie weken.</p>
      <ul><li>geen mascara meer nodig</li><li>waterbestendig</li><li>geschikt voor gevoelige ogen</li><li>zachte en lichte lijm</li><li>behandeling in alle rust</li><li>persoonlijk advies</li><li>nazorgborsteltje inbegrepen</li></ul>
    </div>
    <div class="photo" style="left:340px;top:250px;width:120px;height:70px" role="img" aria-label="Close-up van ogen met wimperverlenging"></div>
  </div>
  <div class="page">
    <div class="photo cool" style="left:0;top:30px;width:490px;height:240px" role="img" aria-label="Schoonheidsspecialiste plaatst wimpers met pincet"></div>
    <div class="bar mint" style="left:30px;top:290px;width:430px"><span>Eerste plaatsing wimperverlenging</span><span class="price">€ 120</span></div>
    <div class="bar rose" style="left:30px;top:320px;width:430px"><span>Bijwerking na twee à drie weken</span><span class="price">€ 45</span></div>
    <div class="brand-mark"><i></i>ATELIER VERANO</div>
  </div>
</section>

<!-- Spread 6 : airbrush tanning -->
<section class="spread" style="top:2410px">
  <div class="page">
    <div class="title rose" style="left:30px;top:24px">Airbrush tanning</div>
    <div class="text" style="left:30px;top:48px;width:170px">
      <p>Een zomerse teint in elk seizoen, zonder schadelijke uv-stralen. Met een fijne nevel wordt een natuurlijke bruiningslotion op de huid aangebracht.</p>
      <p>De kleur ontwikkelt zich in enkele uren en blijft ongeveer een week mooi. Het resultaat is egaal, zonder strepen en volledig aangepast aan uw huidtype.</p>
      <p>Ideaal voor een feest, huwelijk of vakantie. Wij adviseren u graag over de juiste tint en de beste voorbereiding.</p>
    </div>
    <div class="photo" style="left:210px;top:48px;width:280px;height:300px" role="img" aria-label="Portret van een vrouw met gebruinde huid"></div>
  </div>
  <div class="page">
    <div class="bar mint" style="left:30px;top:26px;width:430px"><span>Airbrush tanning met volledige lichaam</span><span class="price">€ 35</span></div>
    <div class="text" style="left:30px;top:50px;width:205px">
      <p>Voor de behandeling: scrub de huid een dag vooraf en gebruik geen crème of deodorant op de dag zelf.</p>
      <p>Draag losse, donkere kledij zodat de kleur rustig kan intrekken.</p>
    </div>
    <div class="text" style="left:255px;top:50px;width:205px">
      <p>Na de behandeling: wacht minstens acht uur met douchen en vermijd zweten of sporten.</p>
      <p>Hydrateer de huid dagelijks om de kleur langer mooi te houden.</p>
    </div>
    <div class="photo round" style="left:200px;top:215px;width:100px;height:100px" role="img" aria-label="Airbrush spuitpistool"></div>
    <div class="brand-mark"><i></i>ATELIER VERANO</div>
  </div>
</section>

<!-- Spread 7 : wimperlifting -->
<section class="spread" style="top:2890px">
  <div class="page">
    <div class="title rose" style="left:30px;top:24px">Wimperlifting Liftline</div>
    <div style="position:absolute;left:30px;top:55px;font-size:12px;letter-spacing:2px;color:var(--ink);font-weight:400">LIFTLINE</div>
    <div class="photo cool" style="left:130px;top:50px;width:330px;height:60px" role="img" aria-label="Ogen voor en na een wimperlifting"></div>
    <div class="bar mint" style="left:30px;top:122px;width:430px;text-transform:none"><span>Lift + Length + Volume = uw natuurlijke wimpers</span></div>
    <div class="text" style="left:30px;top:148px;width:430px">
      <p>Een wimperlifting geeft uw eigen wimpers een mooie krul vanaf de basis. Hierdoor lijken ze langer, voller en donkerder, zonder extensions of mascara.</p>
      <p>De behandeling duurt ongeveer een uur en het resultaat blijft zes tot acht weken zichtbaar. Na afloop kunt u meteen uw dagelijkse activiteiten hervatten.</p>
      <p>Tijdens de behandeling worden de wimpers eerst gereinigd, daarna rond een zacht siliconen kussentje gelegd en met een voedende lotion gefixeerd.</p>
    </div>
  </div>
  <div class="page">
    <div class="text" style="left:30px;top:26px;width:205px">
      <p>De lotion bevat keratine en vitaminen die de wimpers versterken.</p>
      <ul><li>geen dagelijks onderhoud</li><li>ook met lenzen</li><li>geschikt voor korte wimpers</li><li>zwemmen en sporten mag</li></ul>
      <p>Een verfbehandeling kan eraan worden toegevoegd voor extra intensiteit.</p>
    </div>
    <div class="text" style="left:255px;top:26px;width:205px">
      <p>Wat is het verschil met een wimperverlenging? Bij lifting blijven enkel uw eigen wimpers behouden.</p>
      <ul><li>wimperlifting</li><li>wimperlifting met verf</li><li>wenkbrauwlifting</li></ul>
      <p>Vraag gerust naar onze combinatieprijzen bij een volgende afspraak.</p>
    </div>
    <div class="brand-mark"><i></i>ATELIER VERANO</div>
  </div>
</section>

<!-- Spread 8 : suikerontharing -->
<section class="spread" style="top:3370px">
  <div class="page">
    <div class="photo" style="left:0;top:0;width:150px;height:450px" role="img" aria-label="Gladde benen na ontharing"></div>
    <div class="title rose" style="left:175px;top:24px">Ontharing met suiker</div>
    <div class="text" style="left:175px;top:48px;width:290px;color:var(--rose);font-size:8px;font-weight:400">Heeft u een gevoelige huid of last van ingegroeide haartjes? Zoekt u een natuurlijk alternatief voor wax? Dan is suikerontharing iets voor u.</div>
    <div class="text" style="left:175px;top:105px;width:290px">
      <p>Wat zijn de voordelen van suikerontharen?</p>
      <ul><li>de suikerpasta bestaat uit suiker, citroen en water</li><li>minder pijnlijk dan klassieke wax</li><li>geen risico op verbranding</li><li>ook korte haartjes worden verwijderd</li><li>minder roodheid en irritatie</li><li>het haar groeit fijner terug</li><li>geschikt voor elk huidtype</li><li>hygiënisch: elke pasta is voor één klant</li><li>langere periode zonder haargroei</li><li>resten lossen op met water</li></ul>
    </div>
  </div>
  <div class="page">
    <div class="bar rose" style="left:30px;top:30px;width:430px"><span>Wenkbrauwen</span><span class="price">€ 12</span></div>
    <div class="bar mint" style="left:30px;top:55px;width:430px"><span>Wenkbrauwen en bovenlip</span><span class="price">€ 18</span></div>
    <div class="bar rose" style="left:30px;top:80px;width:430px"><span>Bovenlip en kin</span><span class="price">€ 14</span></div>
    <div class="bar mint" style="left:30px;top:105px;width:430px"><span>Bovenlip en kin</span><span class="price">€ 16</span></div>
    <div class="bar rose" style="left:30px;top:130px;width:430px"><span>Gelaat volledig</span><span class="price">€ 28</span></div>
    <div class="bar mint" style="left:30px;top:155px;width:430px"><span>Oksels</span><span class="price">€ 15</span></div>
    <div class="bar rose" style="left:30px;top:180px;width:430px"><span>Armen</span><span class="price">€ 22</span></div>
    <div class="bar mint" style="left:30px;top:205px;width:430px"><span>Bikinilijn</span><span class="price">€ 18</span></div>
    <div class="bar rose" style="left:30px;top:230px;width:430px"><span>Brazilian</span><span class="price">€ 35</span></div>
    <div class="bar mint" style="left:30px;top:255px;width:430px"><span>Onderbenen</span><span class="price">€ 25</span></div>
    <div class="bar rose" style="left:30px;top:280px;width:430px"><span>Bovenbenen</span><span class="price">€ 28</span></div>
    <div class="bar mint" style="left:30px;top:305px;width:430px"><span>Volledige benen</span><span class="price">€ 45</span></div>
    <div class="bar rose" style="left:30px;top:330px;width:430px"><span>Volledige benen en bikinilijn</span><span class="price">€ 58</span></div>
    <div class="brand-mark"><i></i>ATELIER VERANO</div>
  </div>
</section>

<!-- Spread 9 : testimonials -->
<section class="spread single-left" style="top:3850px">
  <div class="page">
    <div class="bar rose" style="left:0;top:30px;width:490px;height:22px;justify-content:center;font-size:10px;letter-spacing:2px">Testimonials</div>
    <div class="testimonial" style="position:absolute;left:70px;top:110px;width:350px">
      <p>“Ik ben al jaren klant en word elke keer met dezelfde zorg ontvangen. Het resultaat is altijd subtiel en prachtig, aanrader!”</p>
      <p class="who">ANNE – VASTE KLANT</p>
    </div>
    <div class="testimonial" style="position:absolute;left:70px;top:190px;width:350px">
      <p>“Super blij met mijn wimpers!”</p>
      <p class="who">ELKE – NIEUWE KLANT</p>
    </div>
  </div>
</section>

</body>
</html>
```